Business Card & Stationary for Jeweller | ||
Copper Lantern Inc. | ||
Use same font as used in my logo | ||
Modern Professional Bright & Fun-filled |
Rosalind Thackeray | ||
President & Principal Designer | ||
By Appointment | ||
rthackeray@copperlanternmail.ca | ||
www.copperlanternmail.ca | ||
Please add: Friendloop Logo plus www.friendloop-example.com/CopperLanternJewellery Chirpster Logo plus @PorchlightMaker LBW (Lapidary Bureau of Westmarch) Logo Fair Ore Alliance Logo **I would like to incorporate a white background with black polka dots somehow on both the business card and stationary. I want glamour, trendy, feminine.** |
We customize each design experience to the clients requirements and bring our expertise and design tools to you! Complimentary Diamond Insurance for 12 months after purchase. Lifetime Manufacturing Warranty Free Lifetime Trade-Up Program Complimentary Champagne Delivery by Appointment Included |

```html
<!DOCTYPE html>
<html lang="en">
<head>
<meta charset="utf-8">
<title>Copper Lantern Inc. — Business Card</title>
<link rel="stylesheet" href="https://fonts.googleapis.com/css2?family=Cormorant+SC:wght@500&family=Cormorant+Garamond:ital,wght@0,500;1,500&family=Open+Sans:wght@400&display=swap">
<style>
  :root {
    --page-bg: #ecebe9;
    --card-bg: #ffffff;
    --brand-pink: #f27bb0;
    --pink-soft: #f7b6d2;
    --rule-grey: #a9a9a9;
    --text-grey: #6e6e6e;
    --white: #ffffff;
  }
  * { margin: 0; padding: 0; box-sizing: border-box; }
  html, body {
    width: 1200px; height: 914px; overflow: hidden;
    background: var(--page-bg);
  }
  .card {
    position: absolute; left: 50px; top: 142px;
    width: 1100px; height: 629px;
    background: var(--card-bg);
    box-shadow: 0 6px 24px rgba(0,0,0,0.12);
  }
  .brand {
    position: absolute; left: 0; right: 0; top: 50px;
    display: flex; flex-direction: column; align-items: center;
  }
  .brand-mark {
    width: 70px; height: 70px; border-radius: 50%;
    border: 3px solid var(--brand-pink);
    margin-bottom: 14px;
  }
  .brand-name {
    font-family: "Cormorant Garamond", serif;
    font-weight: 500;
    font-size: 48px;
    color: var(--brand-pink);
    letter-spacing: 1px;
  }
  .band-rule {
    position: absolute; left: 0; width: 100%; height: 4px;
    background: var(--rule-grey);
  }
  .band-rule.top { top: 322px; }
  .band-rule.bottom { top: 406px; }
  .name-band {
    position: absolute; left: 0; top: 330px; width: 100%; height: 72px;
    background: var(--brand-pink);
    display: flex; align-items: center; justify-content: flex-end;
    padding-right: 160px;
    color: var(--white);
    font-family: "Cormorant SC", serif; font-weight: 500;
  }
  .person-name { font-size: 36px; letter-spacing: 2px; }
  .divider { font-size: 34px; margin: 0 14px; }
  .person-title {
    font-family: "Cormorant Garamond", serif; font-size: 30px;
  }
  .contacts {
    position: absolute; top: 460px; left: 0; width: 100%;
    font-family: "Open Sans", sans-serif; font-size: 21px;
    color: var(--text-grey);
  }
  .contact {
    position: absolute; display: flex; align-items: center; gap: 12px;
    white-space: nowrap;
  }
  .contact svg { width: 26px; height: 26px; flex: none; }
  .contact.email { left: 80px; top: 44px; }
  .contact.phone-main { left: 470px; top: 0; }
  .contact.phone-alt { left: 470px; top: 44px; }
  .contact.web { left: 470px; top: 88px; }
</style>
</head>
<body>
  <main class="card">
    <header class="brand">
      <span class="brand-mark" aria-hidden="true"></span>
      <span class="brand-name">Copper Lantern</span>
    </header>

    <div class="band-rule top"></div>
    <div class="name-band">
      <span class="person-name">Rosalind Thackeray</span>
      <span class="divider">|</span>
      <span class="person-title">President &amp; Principal Designer</span>
    </div>
    <div class="band-rule bottom"></div>

    <section class="contacts">
      <div class="contact phone-main">
        <svg viewBox="0 0 26 26" aria-hidden="true">
          <circle cx="13" cy="13" r="13" fill="var(--brand-pink)"/>
          <path d="M9 7c1 0 2 2.5 2 3s-1 1-1 1.5 2.5 3.5 3.5 3.5 1-1 1.5-1 3 1 3 2-1.5 2-2.5 2C11 18 8 14 8 10c0-1.5.5-3 1-3z" fill="var(--white)"/>
        </svg>
        <span>1-855-555-0142</span>
      </div>
      <div class="contact email">
        <svg viewBox="0 0 26 26" aria-hidden="true">
          <circle cx="13" cy="13" r="13" fill="var(--brand-pink)"/>
          <rect x="7" y="8.5" width="12" height="9" rx="1" fill="var(--white)"/>
          <path d="M7.5 9l5.5 4.5L18.5 9" fill="none" stroke="var(--brand-pink)" stroke-width="1.3"/>
        </svg>
        <span>rthackeray@copperlanternmail.ca</span>
      </div>
      <div class="contact phone-alt">
        <svg viewBox="0 0 26 26" aria-hidden="true">
          <circle cx="13" cy="13" r="13" fill="var(--brand-pink)"/>
          <path d="M9 7c1 0 2 2.5 2 3s-1 1-1 1.5 2.5 3.5 3.5 3.5 1-1 1.5-1 3 1 3 2-1.5 2-2.5 2C11 18 8 14 8 10c0-1.5.5-3 1-3z" fill="var(--white)"/>
        </svg>
        <span>1-855-555-0143</span>
      </div>
      <div class="contact web">
        <svg viewBox="0 0 26 26" aria-hidden="true">
          <circle cx="13" cy="13" r="13" fill="var(--brand-pink)"/>
          <g fill="none" stroke="var(--white)" stroke-width="1.3">
            <circle cx="13" cy="13" r="6"/>
            <ellipse cx="13" cy="13" rx="2.6" ry="6"/>
            <path d="M7 13h12"/>
          </g>
        </svg>
        <span>www.copperlanternmail.ca</span>
      </div>
    </section>
  </main>
</body>
</html>
```